Business Card Design

New business card design

Target Market(s)

Residential & Commercial Property Managers

Industry/Entity Type

Plumbing Services

Contact Information for Business Card

Name - Rowan Keddle, title - Director, Phone Number - 0431 286 517, email - rowan@tbk-plumbing.com.au, Company ABN - 73 215 904 386,

Font styles to use
Sans Serif

Colors
0054AA
0677BA
7BADD7
CADEEF
E8F1F8

```html
<!DOCTYPE html>
<html lang="en">
<head>
<meta charset="utf-8">
<title>TBK Plumbing Services – Business Card</title>
<link href="https://fonts.googleapis.com/css2?family=Montserrat:wght@300;400;600;700&display=swap" rel="stylesheet">
<style>
  :root {
    --backdrop: #2c2c2e;
    --card: #1f242c;
    --card-light: #262c35;
    --accent: #2ea3dc;
    --white: #ffffff;
    --text: #e9eef3;
  }
  * { box-sizing: border-box; margin: 0; padding: 0; }
  html, body {
    width: 1200px; height: 900px; overflow: hidden;
    background: var(--backdrop);
    font-family: "Montserrat", sans-serif;
  }
  .canvas {
    position: relative; width: 1200px; height: 900px;
    display: flex; flex-direction: column; align-items: center;
    justify-content: center; gap: 40px;
  }
  .card {
    position: relative; width: 700px; height: 400px;
    border-radius: 22px;
    background: linear-gradient(160deg, var(--card) 0%, var(--card-light) 100%);
    border-bottom: 6px solid var(--accent);
    overflow: hidden;
  }
  /* Front */
  .card-front { display: flex; align-items: center; justify-content: center; }
  .brand { display: flex; align-items: center; gap: 14px; white-space: nowrap; }
  .brand-dot { width: 18px; height: 18px; border-radius: 50%; background: var(--accent); flex: none; }
  .brand-name {
    color: var(--white); font-weight: 300; letter-spacing: 0.06em;
    font-size: 40px; line-height: 1;
  }
  /* Back */
  .card-back .brand { position: absolute; left: 40px; top: 160px; gap: 8px; }
  .card-back .brand-name { font-size: 18px; letter-spacing: 0.03em; }
  .card-back .brand-dot { width: 11px; height: 11px; }
  .divider {
    position: absolute; left: 338px; top: 70px; width: 2px; height: 200px;
    background: var(--accent);
  }
  .contact { position: absolute; left: 362px; top: 72px; color: var(--text); }
  .contact-name { color: var(--accent); font-weight: 700; font-size: 28px; line-height: 1.1; }
  .contact-title { font-size: 15px; font-weight: 400; margin: 2px 0 14px; }
  .contact-list { list-style: none; }
  .contact-list li {
    display: flex; align-items: center;
    font-size: 15px; font-weight: 400; margin-bottom: 9px;
  }
  .contact-icon { width: 16px; height: 16px; flex: none; margin-right: 12px; }
  .abn { font-size: 15px; margin-top: 4px; }
  .abn strong { font-weight: 700; }
  .band-blue {
    position: absolute; left: 0; bottom: 16px; width: 400px; height: 46px;
    background: var(--accent);
  }
  .band-white {
    position: absolute; left: 412px; bottom: 16px; right: 0; height: 46px;
    background: var(--white);
  }
</style>
</head>
<body>
<main class="canvas">
  <section class="card card-front">
    <div class="brand">
      <span class="brand-dot"></span>
      <span class="brand-name">TBK Plumbing Services</span>
    </div>
  </section>

  <section class="card card-back">
    <div class="brand">
      <span class="brand-dot"></span>
      <span class="brand-name">TBK Plumbing Services</span>
    </div>
    <div class="divider"></div>
    <div class="contact">
      <h1 class="contact-name">Rowan Keddle</h1>
      <p class="contact-title">Director</p>
      <ul class="contact-list">
        <li>
          <svg class="contact-icon" viewBox="0 0 24 24" aria-hidden="true"><path fill="#2ea3dc" d="M6.6 10.8a15 15 0 0 0 6.6 6.6l2.2-2.2c.3-.3.7-.4 1-.2 1.1.4 2.3.6 3.6.6.6 0 1 .4 1 1V20c0 .6-.4 1-1 1C10.6 21 3 13.4 3 4c0-.6.4-1 1-1h3.5c.6 0 1 .4 1 1 0 1.3.2 2.5.6 3.6.1.3 0 .7-.2 1z"/></svg>
          <span class="contact-text">0431 286 517</span>
        </li>
        <li>
          <svg class="contact-icon" viewBox="0 0 24 24" aria-hidden="true"><path fill="#2ea3dc" d="M3 6h18v12H3z"/><path fill="none" stroke="#1f242c" stroke-width="1.8" d="M3 6l9 7 9-7"/></svg>
          <span class="contact-text">rowan@tbk-plumbing.com.au</span>
        </li>
        <li>
          <svg class="contact-icon" viewBox="0 0 24 24" aria-hidden="true"><circle cx="12" cy="12" r="10" fill="#2ea3dc"/><path fill="none" stroke="#1f242c" stroke-width="1.4" d="M2 12h20M12 2c3 3 3 17 0 20M12 2c-3 3-3 17 0 20"/></svg>
          <span class="contact-text">www.tbk-plumbing.com.au</span>
        </li>
      </ul>
      <p class="abn"><strong>ABN</strong> - 73 215 904 386</p>
    </div>
    <div class="band-blue"></div>
    <div class="band-white"></div>
  </section>
</main>
</body>
</html>
```